Hi everyone,
Fresh Walls Co is a business that renovates older houses into modern homes. I'm looking for a design that is clean and simple. It needs to show the client that renovating is a simple process. No more than 3 colours to be used thanks.

What I need:
1. Logo
2. Business card (one side)
3. Letter head (A4)

Looking forward to the designs!

Construction

Fresh Walls Co

Sans Serif

Must have
• Trading name: Fresh Walls Co
• Contact name: Declan Ashworth
• Email: declanashworth@freshwallsco.example.com.au
• Tel: 0412 758 204
• Clean and simple
Nice to have
• If design might include a few tools. eg Hammer, paint roller etc.
Should not have
• Complicated design

```html
<!DOCTYPE html>
<html lang="en">
<head>
<meta charset="UTF-8">
<title>Fresh Walls Co — Business Card</title>
<link rel="stylesheet" href="https://fonts.googleapis.com/css2?family=Roboto+Condensed:wght@400;700&display=swap">
<style>
  :root {
    --orange: #f28c13;
    --charcoal: #58595b;
    --white: #ffffff;
    --backdrop: #e9e7e4;
  }
  html, body {
    margin: 0;
    padding: 0;
    width: 1200px;
    height: 800px;
    overflow: hidden;
    background: var(--backdrop);
    font-family: "Roboto Condensed", "Arial Narrow", sans-serif;
  }
  .canvas {
    width: 1200px;
    height: 800px;
    display: flex;
    align-items: center;
    justify-content: center;
  }
  .business-card {
    width: 900px;
    height: 514px;
    background: var(--white);
    display: grid;
    grid-template-rows: 250px 86px 1fr;
    box-shadow: 0 12px 30px rgba(0,0,0,0.18);
    overflow: hidden;
  }
  .brand {
    display: flex;
    align-items: center;
    justify-content: center;
    gap: 18px;
    padding-top: 30px;
  }
  .brand-mark {
    width: 46px;
    height: 46px;
    background: var(--orange);
  }
  .brand-name {
    font-weight: 700;
    font-size: 64px;
    line-height: 1;
    color: var(--orange);
    letter-spacing: 0.5px;
  }
  .name-row {
    display: grid;
    grid-template-columns: 1fr 330px;
  }
  .contact-name {
    background: var(--charcoal);
    color: var(--white);
    font-weight: 700;
    font-size: 40px;
    letter-spacing: 1px;
    text-transform: uppercase;
    display: flex;
    align-items: center;
    padding-left: 200px;
  }
  .phone {
    background: var(--orange);
    color: var(--white);
    font-size: 30px;
    display: flex;
    align-items: center;
    gap: 16px;
    padding-left: 24px;
  }
  .phone svg { flex: none; }
  .email-row {
    background: var(--orange);
    color: var(--white);
    font-size: 26px;
    display: flex;
    align-items: center;
    padding-left: 60px;
  }
</style>
</head>
<body>
<main class="canvas">
  <section class="business-card">
    <header class="brand">
      <span class="brand-mark" aria-hidden="true"></span>
      <span class="brand-name">Fresh Walls Co</span>
    </header>
    <div class="name-row">
      <div class="contact-name">Declan Ashworth</div>
      <div class="phone">
        <svg class="icon-mail" width="38" height="26" viewBox="0 0 38 26" aria-hidden="true">
          <rect x="1.5" y="1.5" width="35" height="23" fill="none" stroke="#ffffff" stroke-width="3"/>
          <polyline points="2,2 19,15 36,2" fill="none" stroke="#ffffff" stroke-width="3"/>
        </svg>
        <span class="phone-number">0412 758 204</span>
        <svg class="icon-phone" width="20" height="28" viewBox="0 0 20 28" aria-hidden="true">
          <path d="M6 2 L10 2 L10 8 L7 9 Q7 15 10 19 L13 18 L16 23 L12 26 Q2 20 2 6 Z" fill="#ffffff"/>
        </svg>
      </div>
    </div>
    <div class="email-row">declanashworth@freshwallsco.example.com.au</div>
  </section>
</main>
</body>
</html>
```